New Innovative Counselling and psychotherapy Service needs Business Card design

Keep it simple and professional. On one side, just company name and logo (perhaps in all blue) and maybe a tag line.

On other side (all white) my name and Qualifications in centre

Industry/Entity Type

Health And Wellness

Contact Information for Business Card

Dara Whelby
Counsellor & Psychotherapist
BSc (Psychol.), BA, Dip. (Couns. & Psych.), PG.Cert (CBT), FGTrK, ONRE

I will also require Mobile no, Email and web site address of which I'll pass on to final designer.

Font styles to use
Sans Serif

Requirements
Must have
• My Logo Only and please use the colours in logo that is in it.
Should not have
• Any other images

```html
<!DOCTYPE html>
<html lang="en">
<head>
<meta charset="utf-8">
<title>Thrive Lane — Business Card</title>
<link rel="stylesheet" href="https://fonts.googleapis.com/css2?family=Arimo:wght@400;700&family=Raleway:wght@400&family=Roboto:wght@400&display=swap">
<style>
  :root {
    --backdrop: #b8b8b8;
    --charcoal: #363636;
    --paper: #f2f2f2;
    --sky: #47b4ed;
    --leaf: #8fd14f;
    --ink: #3a3a3a;
    --white: #ffffff;
  }
  * { margin: 0; padding: 0; box-sizing: border-box; }
  html, body {
    width: 1200px; height: 960px; overflow: hidden;
    background: var(--backdrop);
  }
  .card {
    position: absolute;
    width: 600px; height: 342px;
    border-radius: 18px;
    overflow: hidden;
  }
  .card--front { left: 322px; top: 110px; background: var(--charcoal); }
  .card--back  { left: 320px; top: 493px; background: var(--sky); }

  .card__curve { position: absolute; inset: 0; }

  .identity {
    position: absolute; left: 21px; top: 94px;
    font-family: "Arimo", Arial, sans-serif;
  }
  .identity__name { font-size: 24px; font-weight: 700; color: var(--sky); line-height: 1.1; }
  .identity__role { font-size: 15px; color: var(--leaf); margin-top: 6px; }
  .identity__quals { font-size: 12px; color: var(--leaf); line-height: 1.25; margin-top: 2px; }

  .contacts { list-style: none; margin-top: 16px; }
  .contacts__item {
    display: flex; align-items: center; gap: 7px;
    font-size: 14px; color: var(--white); line-height: 19.5px;
  }
  .contacts__icon { width: 14px; height: 14px; flex: none; }

  .brand {
    position: absolute; display: flex; align-items: center; gap: 12px;
    font-family: "Raleway", sans-serif; font-weight: 400;
  }
  .brand--front { left: 341px; top: 150px; }
  .brand--front .brand__dot { width: 38px; height: 38px; border-radius: 50%; background: var(--sky); }
  .brand--front .brand__name { font-size: 23px; color: var(--ink); }

  .brand--back { left: 0; right: 0; top: 120px; justify-content: center; gap: 18px; }
  .brand--back .brand__dot { width: 70px; height: 70px; border-radius: 50%; background: var(--white); }
  .brand--back .brand__name { font-size: 44px; color: var(--white); }

  .tagline {
    position: absolute; left: 0; right: 0; top: 288px;
    text-align: center;
    font-family: "Roboto", sans-serif; font-size: 14px; color: var(--white);
  }
</style>
</head>
<body>

<section class="card card--front">
  <svg class="card__curve" viewBox="0 0 600 342" width="600" height="342" aria-hidden="true">
    <path d="M358 0 Q212 171 348 342 L600 342 L600 0 Z" fill="#ffffff"/>
    <path d="M362 0 Q218 171 352 342 L600 342 L600 0 Z" fill="#8fd14f"/>
    <path d="M362 0 Q228 171 375 342 L600 342 L600 0 Z" fill="#47b4ed"/>
    <path d="M374 0 Q236 171 384 342 L600 342 L600 0 Z" fill="#ffffff"/>
    <path d="M380 0 Q242 171 390 342 L600 342 L600 0 Z" fill="#f2f2f2"/>
  </svg>

  <div class="identity">
    <h1 class="identity__name">Dara Whelby</h1>
    <p class="identity__role">Counsellor &amp; Psychotherapist</p>
    <p class="identity__quals">BSc (Psychol.), BA, Dip. (Couns. &amp; Psych.)<br>PG.Cert (CBT), FGTrK,</p>
    <ul class="contacts">
      <li class="contacts__item">
        <svg class="contacts__icon" viewBox="0 0 14 14"><rect x="3.5" y="0.5" width="7" height="13" rx="1.2" fill="none" stroke="#fff" stroke-width="1.4"/><rect x="5" y="2.2" width="4" height="8" fill="#fff"/></svg>
        555 210 4781
      </li>
      <li class="contacts__item">
        <svg class="contacts__icon" viewBox="0 0 14 14"><rect x="1" y="3.5" width="12" height="8" fill="#fff"/><path d="M1 3.5 L7 8 L13 3.5" fill="none" stroke="#363636" stroke-width="1.2"/></svg>
        dara@Thrivelane.com
      </li>
      <li class="contacts__item">
        <svg class="contacts__icon" viewBox="0 0 14 14"><circle cx="7" cy="7" r="6" fill="#fff"/><path d="M4 4 Q6 6 5 8 Q8 9 9 12 M9 3 Q8 5 11 6" fill="none" stroke="#363636" stroke-width="1.3"/></svg>
        www.Thrivelane.com
      </li>
    </ul>
  </div>

  <div class="brand brand--front">
    <span class="brand__dot"></span>
    <span class="brand__name">Thrive Lane</span>
  </div>
</section>

<section class="card card--back">
  <div class="brand brand--back">
    <span class="brand__dot"></span>
    <span class="brand__name">Thrive Lane</span>
  </div>
  <p class="tagline">Caring For Your Psychological Well-Being Is Our Top Priority</p>
</section>

</body>
</html>
```